kmvalerohub website

I need a new homepage design for my current website at www.KMValeroHub.com. I want someone to look at my current website and develop a more appealing homepage... right now the colors don't blend very well and it needs a facelift

Reason: This has been extended to September 10th

```html
<!DOCTYPE html>
<html lang="en">
<head>
<meta charset="utf-8">
<title>KM Valero – Home</title>
<link rel="stylesheet" href="https://fonts.googleapis.com/css2?family=Noto+Sans:wght@400;700&family=Great+Vibes&display=swap">
<style>
  :root{
    --page-dark:#3a3a3a;
    --page-dark-2:#2c2c2c;
    --sky-top:#0e4fb3;
    --sky-mid:#2f7fe0;
    --sky-low:#1a5fc8;
    --accent-green:#b5cf1e;
    --brand-blue:#2a5faa;
    --link-blue:#1f63b8;
    --ink:#222;
    --body-text:#333;
    --rule:#2b5ea8;
    --panel:#f7f7f7;
    --panel-border:#dcdcdc;
    --footer:#2b63b0;
    --white:#fff;
  }
  *{box-sizing:border-box;margin:0;padding:0}
  html,body{width:1200px;height:1135px;overflow:hidden}
  body{position:relative;background:var(--white);font-family:"Noto Sans",Arial,sans-serif;color:var(--body-text)}

  .top-band{position:absolute;left:0;top:0;width:1200px;height:436px;
    background:repeating-linear-gradient(90deg,var(--page-dark) 0 2px,var(--page-dark-2) 2px 4px);}
  .top-band::after{content:"";position:absolute;left:0;top:376px;width:100%;height:60px;background:#262626}

  .hero{position:absolute;left:117px;top:0;width:978px;height:376px;
    background:linear-gradient(180deg,var(--sky-top) 0%,var(--sky-mid) 55%,var(--sky-low) 100%);}
  .hero-photo{position:absolute;left:17px;top:100px;width:900px;height:290px;
    background:radial-gradient(ellipse at 40% 35%,rgba(181,207,30,.55),rgba(181,207,30,0) 45%),
               radial-gradient(ellipse at 88% 55%,rgba(235,225,210,.35),rgba(235,225,210,0) 30%);}

  .social{position:absolute;top:12px;left:927px;display:flex;gap:16px}
  .social span{display:block;width:30px;height:30px;border-radius:50%;background:#1b57b8;border:2px solid #cfe2f7}

  .nav{position:absolute;left:69px;top:50px;width:826px;height:50px;
    background:linear-gradient(180deg,#3a3a3a,#050505);border-bottom:3px solid var(--accent-green);
    border-radius:2px;display:flex;align-items:center}
  .brand{margin-left:14px;font-size:28px;font-weight:400;color:var(--white);letter-spacing:1px}
  .nav ul{list-style:none;display:flex;margin-left:auto;margin-right:12px;gap:0}
  .nav li{font-size:13.5px;color:var(--white);padding:0 12px}

  .tagline{position:absolute;left:55px;top:328px;color:var(--white);font-size:17px;font-weight:700;
    display:flex;align-items:baseline;gap:10px;white-space:nowrap}
  .tagline .script{font-family:"Great Vibes",cursive;font-weight:400;font-size:26px}

  .subscribe{position:absolute;left:117px;top:376px;width:978px;height:60px;background:rgba(30,70,130,.55);
    display:flex;align-items:center;color:var(--white);font-size:13.5px;font-weight:700}
  .subscribe label{margin-left:70px}
  .subscribe label + .field{margin-left:6px}
  .subscribe .field{width:166px;height:18px;background:var(--white);border:1px solid #999}
  .subscribe .email{margin-left:10px}
  .subscribe .btn{margin-left:26px;width:97px;height:28px;border-radius:14px;background:#1c4f8f;
    border:1px solid #5d8ccc;font-size:12px;font-weight:400;display:flex;align-items:center;justify-content:center}
  .subscribe label.email-label{margin-left:60px}

  .features{position:absolute;left:187px;top:466px;display:flex;gap:27px}
  .feature{width:257px}
  .feature h2{font-size:17px;font-weight:400;color:var(--ink);padding-bottom:4px;border-bottom:5px solid var(--rule)}
  .feature p{font-size:10.5px;line-height:20.5px;margin-top:9px;height:85px}
  .more{font-size:11px;color:var(--link-blue);font-weight:700;display:block;margin-top:12px}

  .contact-strip{position:absolute;left:187px;top:660px;width:825px;height:56px;background:var(--panel);
    border:1px solid var(--panel-border);border-radius:3px;display:flex;align-items:center;font-size:12px;color:var(--ink)}
  .contact-strip .item{display:flex;align-items:center;gap:12px;margin-left:10px}
  .contact-strip .item + .item{margin-left:20px}

  .reel{position:absolute;left:186px;top:767px;width:406px;height:268px;background:#f3f3f3;border:1px solid #d5d5d5;
    box-shadow:0 1px 3px rgba(0,0,0,.15)}
  .reel-photo{position:absolute;left:9px;top:9px;width:387px;height:213px;
    background:linear-gradient(120deg,#1c5fc4 0%,#2f7be0 55%,#6b4a3a 75%,#b43a3a 100%)}
  .reel-title{position:absolute;left:12px;bottom:22px;color:var(--white);font-size:20px;font-weight:700}
  .reel-sub{position:absolute;left:12px;bottom:6px;color:var(--white);font-size:11.5px}
  .player{position:absolute;left:9px;top:228px;width:387px;height:32px;display:flex;align-items:center}
  .play{width:30px;height:30px;border-radius:50%;border:1px solid #bbb;background:linear-gradient(#fff,#e3e3e3);
    display:flex;align-items:center;justify-content:center}
  .track{margin-left:8px;width:285px;height:14px;border:1px solid #bbb;background:var(--white);position:relative}
  .track::before{content:"";position:absolute;left:14px;top:1px;width:5px;height:10px;background:var(--link-blue)}
  .time{margin-left:12px;font-size:10px;color:#555}

  .media{position:absolute;left:608px;top:762px;width:410px}
  .media h2{font-size:21px;font-weight:400;color:var(--ink)}
  .media-grid{display:grid;grid-template-columns:210px 200px;row-gap:14px;margin-top:12px}
  .media-item h3{font-size:15px;font-weight:400;color:#333;display:flex;align-items:center;gap:4px}
  .media-item p{font-size:10.5px;line-height:18px;margin-top:4px;width:195px}
  .cta{display:inline-block;margin-top:8px;font-size:17px;color:var(--ink);text-decoration:underline}

  .footer{position:absolute;left:0;top:1073px;width:1200px;height:62px;background:var(--footer);
    color:var(--white);font-size:11.5px;display:flex;align-items:center;justify-content:center}
</style>
</head>
<body>
  <div class="top-band"></div>

  <header class="hero">
    <div class="hero-photo" role="img" aria-label="Woman leaping against a blue sky holding a flowing green scarf"></div>
    <div class="social">
      <span role="img" aria-label="Social network link"></span>
      <span role="img" aria-label="Social network link"></span>
    </div>
    <nav class="nav">
      <div class="brand">KM Valero</div>
      <ul>
        <li>Home</li><li>Products</li><li>About</li><li>Blog</li><li>Forum</li><li>Media Room</li><li>Success Stories</li><li>Contact Us</li>
      </ul>
    </nav>
    <div class="tagline">
      <span class="script">Discover</span><span>SECRETS TO A</span>
      <span class="script">Slimmer Sexier</span><span>&amp; HEALTHIER YOU!</span>
    </div>
  </header>

  <form class="subscribe">
    <label>Name :</label><span class="field"></span>
    <label class="email-label" style="margin-left:14px">Email :</label><span class="field" style="margin-left:6px"></span>
    <span class="btn">SUBSCRIBE</span>
  </form>

  <section class="features">
    <article class="feature">
      <h2>10-Day Cleanse</h2>
      <p>Cras volutpat quam et neque ultrices mattis. Mauris turpis urna, consequat id feugiat vitae, tempor ac nunc. Proin quis nisi eget nulla suscipit tempus eu sit amet sem. Suspendisse sit amet</p>
      <span class="more">Learn More »</span>
    </article>
    <article class="feature">
      <h2>ABOUT KM VALERO</h2>
      <p>Cras volutpat quam et neque ultrices mattis. Mauris turpis urna, consequat id feugiat vitae, tempor ac nunc. Proin quis nisi eget nulla suscipit tempus eu sit amet sem.</p>
      <span class="more">Learn More »</span>
    </article>
    <article class="feature">
      <h2>Success Stories</h2>
      <p>Cras volutpat quam et neque ultrices mattis. Mauris turpis urna, consequat id feugiat vitae, tempor ac nunc. Proin quis nisi eget nulla.</p>
      <span class="more">Learn More »</span>
    </article>
  </section>

  <div class="contact-strip">
    <div class="item">
      <svg width="20" height="16" viewBox="0 0 20 16"><path d="M1 5c0-3 18-3 18 0v2h-5V5H6v2H1z" fill="#333"/><path d="M4 8h12l2 7H2z" fill="#333"/><circle cx="10" cy="11" r="2" fill="#f7f7f7"/></svg>
      <span>For customer service support, contact info@kmvalerohub.com</span>
    </div>
    <div class="item">
      <svg width="20" height="16" viewBox="0 0 20 16"><path d="M1 5c0-3 18-3 18 0v2h-5V5H6v2H1z" fill="#333"/><path d="M4 8h12l2 7H2z" fill="#333"/><circle cx="10" cy="11" r="2" fill="#f7f7f7"/></svg>
      <span>Media Phone: 202-555-0187 (only media inquiries will get a return call)</span>
    </div>
  </div>

  <div class="reel">
    <div class="reel-photo" role="img" aria-label="Promotional video still of a guest holding a smoothie cleanse book">
      <div class="reel-title">KM'S DEMO REEL</div>
      <div class="reel-sub">KM is a fabulous guest on radio and TV,</div>
    </div>
    <div class="player">
      <span class="play"><svg width="12" height="14" viewBox="0 0 12 14"><path d="M1 0l11 7-11 7z" fill="#1f63b8"/></svg></span>
      <span class="track"></span>
      <span class="time">0:00 / 0:00</span>
    </div>
  </div>

  <section class="media">
    <h2>Media Room</h2>
    <div class="media-grid">
      <div class="media-item">
        <h3><svg width="24" height="24" viewBox="0 0 24 24"><path d="M11 3a10 10 0 1 0 10 10H11z" fill="#333"/><path d="M13 1v10h10A10 10 0 0 0 13 1z" fill="#333"/></svg>KM's Demo Reel</h3>
        <p>Cras volutpat quam et neque ultrices mattis. Mauris turpis urna, consequat id feugiat vitae, tempor ac nunc. Proin</p>
      </div>
      <div class="media-item">
        <h3><svg width="24" height="24" viewBox="0 0 24 24"><circle cx="12" cy="7" r="5" fill="#333"/><path d="M2 23c0-7 4-10 10-10s10 3 10 10z" fill="#333"/></svg>KM's Press Kit</h3>
        <p>Cras volutpat quam et neque ultrices mattis. Mauris turpis urna, consequat id feugiat vitae, tempor ac nunc. Proin</p>
      </div>
      <div class="media-item">
        <h3><svg width="28" height="22" viewBox="0 0 28 22"><circle cx="7" cy="8" r="3.5" fill="#333"/><circle cx="21" cy="8" r="3.5" fill="#333"/><circle cx="14" cy="6" r="4" fill="#333"/><path d="M0 20c0-5 3-7 7-7s7 2 7 7z M14 20c0-5 3-7 7-7s7 2 7 7z M6 21c0-6 3-9 8-9s8 3 8 9z" fill="#333"/></svg>KM's Speaker Reel</h3>
        <p>Cras volutpat quam et neque ultrices mattis. Mauris turpis urna, consequat id feugiat vitae, tempor ac nunc. Proin</p>
      </div>
      <div class="media-item">
        <h3><svg width="24" height="24" viewBox="0 0 24 24"><circle cx="12" cy="12" r="10" fill="none" stroke="#333" stroke-width="5"/><circle cx="12" cy="12" r="10" fill="none" stroke="#fff" stroke-width="5" stroke-dasharray="5 10.7"/></svg>Metro Weekend Today</h3>
        <p>Cras volutpat quam et neque ultrices mattis. Mauris turpis urna, consequat id feugiat vitae, tempor ac nunc. Proin</p>
      </div>
    </div>
    <span class="cta">Integrate Your Business Model With KM VALERO Now</span>
  </section>

  <footer class="footer">Privacy Policy | Terms of Use | Disclaimer | Copyright © 2011 Corvella Publishing</footer>
</body>
</html>
```